Merry Meadow Roasters

We need a website to sell coffee with a horse theme. We already have a logo and have designed 4 different coffee bags/flavors so far, each of which will be available in ground or whole bean. The brand is intended to be light hearted/whimsical.

Requirements
Must have
• incorporation of attached photos
Nice to have
• underlying background theme with sky/grass

```html
<!DOCTYPE html>
<html lang="en">
<head>
<meta charset="utf-8">
<title>Merry Meadow Roasters</title>
<link rel="stylesheet" href="https://fonts.googleapis.com/css2?family=Amatic+SC:wght@700&family=Montserrat:wght@400;500&display=swap">
<style>
:root{
  --ink:#3a2a20;
  --text:#5b4a40;
  --muted:#7a6a60;
  --accent:#c9803a;
  --tan:#ecd0a6;
  --line:#c9a67a;
  --price:#d49a55;
  --about-bg:#f2e4d9;
  --testi-bg:#eee1d7;
  --footer-bg:#faf3ee;
  --sale:#b5471c;
  --frame:#b89272;
  --white:#ffffff;
}
*{margin:0;padding:0;box-sizing:border-box}
html,body{width:1200px;height:4169px;overflow:hidden;background:var(--white)}
body{position:relative;font-family:"Montserrat",sans-serif;color:var(--text)}
.abs{position:absolute}
.display{font-family:"Amatic SC",cursive;font-weight:700;color:var(--ink);letter-spacing:1px}
.section-title{position:absolute;left:0;width:1200px;text-align:center;font-size:44px;line-height:1}
.divider{position:absolute;left:500px;width:200px;height:8px}
.lead{position:absolute;left:0;width:1200px;text-align:center;font-size:15px;line-height:23px;color:var(--text)}
.btn{position:absolute;background:var(--tan);color:var(--ink);font-size:16px;font-weight:500;display:flex;align-items:center;justify-content:center}
.ph{position:absolute}

/* hero */
.hero{position:absolute;left:0;top:0;width:1200px;height:546px;background:linear-gradient(100deg,#2b1c14 0%,#4a3224 45%,#6b4a35 70%,#3d281c 100%)}
.nav{position:absolute;left:113px;top:55px;width:975px;height:57px;background:#faf5f0;border-radius:29px}
.nav a{position:absolute;top:20px;font-size:14px;color:var(--ink);text-decoration:none}
.nav .active{color:var(--accent);font-weight:500}
.logo-badge{position:absolute;left:113px;top:27px;width:112px;height:112px;border-radius:50%;background:#faf5f0;display:flex;align-items:center;justify-content:center;text-align:center;font-size:13px;font-weight:500;color:var(--ink);line-height:16px}

/* offer */
.offer-item{position:absolute;width:230px;text-align:center}
.offer-item h3{font-size:19px;font-weight:500;color:var(--ink);margin-top:22px}
.offer-item p{font-size:13px;line-height:20px;color:var(--muted);margin-top:14px}

/* products */
.card{position:absolute;top:1996px;width:225px;height:416px;border:1px solid #cfc6c0;text-align:center}
.card.featured{background:#fdf3ea;border-color:#fdf3ea}
.card h4{position:absolute;top:237px;width:100%;font-family:"Amatic SC",cursive;font-size:30px;color:var(--ink)}
.card p{position:absolute;top:272px;width:100%;font-size:12px;line-height:16px;color:var(--muted)}
.card .price{position:absolute;top:318px;width:100%;font-size:16px;color:var(--price)}
.card .price s{color:var(--muted);margin-right:6px}

/* blog */
.post{position:absolute;top:3442px;width:298px}
.post h5{font-size:20px;font-weight:500;line-height:28px;color:var(--ink);margin-top:42px}
.post p{font-size:13px;line-height:20px;color:var(--muted);margin-top:16px}

.foot-links a{position:absolute;top:4083px;font-size:16px;color:var(--ink);text-decoration:none}
</style>
</head>
<body>

<!-- Hero -->
<section class="hero">
  <div class="ph" role="img" aria-label="Coffee cup and coffee bag on a wooden table" style="left:700px;top:200px;width:470px;height:346px;background:radial-gradient(ellipse at 60% 55%,#c9a88a 0%,#7a5640 45%,rgba(60,40,28,0) 75%)"></div>
  <h1 class="abs display" style="left:110px;top:212px;font-size:48px;line-height:54px;color:#fff;width:560px">SADDLE UP FOR THE BEST COFFEE RIDE OF YOUR LIFE</h1>
  <p class="abs" style="left:111px;top:341px;width:520px;font-size:15px;line-height:23px;color:#fff">Lorem ipsum dolor sit amet, consectetur adipiscing elit, sed do eiusmod tempor incididunt ut labore et dolore</p>
  <div class="btn" style="left:111px;top:400px;width:154px;height:38px">Shop Now</div>
</section>

<nav class="nav">
  <a class="active" style="left:377px">Home</a>
  <div class="abs" style="left:376px;top:53px;width:46px;height:3px;background:var(--accent)"></div>
  <a style="left:469px">Shop</a>
  <a style="left:553px">About Us</a>
  <a style="left:666px">Blog</a>
  <a style="left:746px">Contact Us</a>
  <svg class="abs" style="left:871px;top:18px" width="22" height="20" viewBox="0 0 22 20"><path d="M1 2h4l3 10h10l2-7H7" fill="none" stroke="#3a2a20" stroke-width="2"/><circle cx="9" cy="16" r="1.8" fill="#3a2a20"/><circle cx="17" cy="16" r="1.8" fill="#3a2a20"/></svg>
  <div class="abs" style="left:887px;top:9px;width:14px;height:14px;border-radius:50%;background:var(--accent);color:#fff;font-size:9px;text-align:center;line-height:14px">0</div>
  <svg class="abs" style="left:917px;top:18px" width="18" height="18" viewBox="0 0 18 18"><circle cx="7" cy="7" r="5" fill="none" stroke="#3a2a20" stroke-width="2"/><path d="M11 11l5 5" stroke="#3a2a20" stroke-width="2.4"/></svg>
</nav>
<div class="logo-badge">Merry<br>Meadow<br>Roasters</div>

<!-- Offer -->
<h2 class="section-title display" style="top:625px">OUR DELICIOUS OFFER</h2>
<svg class="divider" style="top:680px" viewBox="0 0 200 8"><path d="M0 4h20M30 4h20M60 4h80M150 4h20M180 4h20" stroke="#c9a67a" stroke-width="3"/></svg>
<p class="lead" style="top:719px">Lorem ipsum dolor sit amet, consectetur adipiscing elit, sed do eiusmod<br>ut labore et dolore magna aliqua. Quis ipsum suspendisse ultrices gravida. Risus commodo viverra</p>

<div class="ph" role="img" aria-label="Faint horse line drawing decoration" style="left:1040px;top:790px;width:160px;height:370px;background:linear-gradient(180deg,rgba(236,226,218,0.6),rgba(236,226,218,0.2))"></div>

<div class="offer-item" style="left:100px;top:810px">
  <div role="img" aria-label="Coffee cup line illustration" style="margin:0 auto;width:130px;height:145px;background:#f6ebe0;border-radius:10px"></div>
  <h3>Types of Coffee</h3><p>Lorem ipsum dolor sit<br>amet, consectetur adipiscing<br>sed do eiusmod</p>
</div>
<div class="offer-item" style="left:356px;top:810px">
  <div role="img" aria-label="Coffee beans line illustration" style="margin:0 auto;width:130px;height:145px;background:#f6ebe0;border-radius:10px"></div>
  <h3>Bean Varieties</h3><p>Lorem ipsum dolor sit<br>amet, consectetur adipiscing<br>sed do eiusmod</p>
</div>
<div class="offer-item" style="left:614px;top:810px">
  <div role="img" aria-label="Coffee bag line illustration" style="margin:0 auto;width:130px;height:145px;background:#f6ebe0;border-radius:10px"></div>
  <h3>Coffee Bag</h3><p>Lorem ipsum dolor sit<br>amet, consectetur adipiscing<br>sed do eiusmod</p>
</div>
<div class="offer-item" style="left:870px;top:810px">
  <div role="img" aria-label="Takeaway coffee cup line illustration" style="margin:0 auto;width:130px;height:145px;background:#f6ebe0;border-radius:10px"></div>
  <h3>Coffee To Go</h3><p>Lorem ipsum dolor sit<br>amet, consectetur adipiscing<br>sed do eiusmod</p>
</div>

<!-- About -->
<section class="abs" style="left:0;top:1172px;width:1200px;height:554px;background:linear-gradient(90deg,#f4e9e0 0%,var(--about-bg) 50%,#e9d8cb 100%)">
  <div class="ph" role="img" aria-label="Coffee bag with scattered beans and a cartoon pony" style="left:0;top:26px;width:534px;height:438px;background:radial-gradient(ellipse at 45% 55%,#c9a27e 0%,#e3c8ab 45%,rgba(242,228,217,0) 75%)"></div>
  <h2 class="abs display" style="left:602px;top:82px;font-size:44px">ABOUT US</h2>
  <svg class="abs" style="left:602px;top:136px" width="210" height="8" viewBox="0 0 210 8"><path d="M0 4h20M30 4h140M180 4h12M198 4h12" stroke="#c9a67a" stroke-width="3"/></svg>
  <p class="abs" style="left:604px;top:183px;width:486px;font-size:15px;line-height:23px">Sed ut perspiciatis unde omnis iste natus error sit voluptatem accusantium doloremque laudantium, totam rem aperiam, eaque ipsa quae ab illo inventore veritatis et quasi architecto beatae vitae dicta sunt explicabo. Nemo enim ipsam voluptatem quia voluptas sit aspernatur aut odit aut fugit, sed quia consequuntur magni dolores eos qui ratione voluptatem sequi nesciunt. Neque porro quisquam est, qui dolorem ipsum quia dolor sit amet, consectetur, adipisci velit, sed quia non numquam eius modi tempora incidunt ut labore et dolore magnam aliquam quaerat voluptatem.</p>
  <div class="btn" style="left:604px;top:426px;width:152px;height:39px">Read More</div>
</section>

<!-- Products -->
<h2 class="section-title display" style="top:1806px">OUR PRODUCTS</h2>
<svg class="divider" style="top:1862px" viewBox="0 0 200 8"><path d="M0 4h20M30 4h20M60 4h80M150 4h20M180 4h20" stroke="#c9a67a" stroke-width="3"/></svg>
<p class="lead" style="top:1901px">Lorem ipsum dolor sit amet, consectetur adipiscing elit, sed do eiusmod<br>ut labore et dolore magna aliqua. Quis ipsum suspendisse ultrices gravida. Risus commodo viverra</p>

<div class="card" style="left:112px">
  <div class="ph" role="img" aria-label="Meadow Morning coffee bag" style="left:53px;top:57px;width:118px;height:162px;background:linear-gradient(180deg,#c9a283,#a47a5c)"></div>
  <h4>MEADOW MORNING</h4><p>Lorem ipsum dolor<br>amet, consectetur adipiscing</p>
  <div class="price"><s>$23.00</s>$19.00</div>
  <div class="btn" style="left:35px;top:350px;width:153px;height:39px">Add To Cart</div>
</div>
<div class="card featured" style="left:363px">
  <div class="abs" style="right:0;top:12px;width:70px;height:24px;background:var(--sale);color:#fff;font-size:12px;font-weight:500;line-height:24px">SALE</div>
  <div class="ph" role="img" aria-label="Pony Prance coffee bag" style="left:53px;top:57px;width:118px;height:162px;background:linear-gradient(180deg,#c9a283,#a47a5c)"></div>
  <h4>PONY PRANCE</h4><p>Lorem ipsum dolor<br>amet, consectetur adipiscing</p>
  <div class="price"><s>$23.00</s>$19.00</div>
  <div class="btn" style="left:35px;top:350px;width:153px;height:39px">Add To Cart</div>
</div>
<div class="card" style="left:613px">
  <div class="ph" role="img" aria-label="Hay Bale Blend coffee bag" style="left:53px;top:57px;width:118px;height:162px;background:linear-gradient(180deg,#c9a283,#a47a5c)"></div>
  <h4>HAY BALE BLEND</h4><p>Lorem ipsum dolor<br>amet, consectetur adipiscing</p>
  <div class="price"><s>$23.00</s>$19.00</div>
  <div class="btn" style="left:35px;top:350px;width:153px;height:39px">Add To Cart</div>
</div>
<div class="card" style="left:864px">
  <div class="ph" role="img" aria-label="Gallop Roast coffee bag" style="left:53px;top:57px;width:118px;height:162px;background:linear-gradient(180deg,#c9a283,#a47a5c)"></div>
  <h4>GALLOP ROAST</h4><p>Lorem ipsum dolor<br>amet, consectetur adipiscing</p>
  <div class="price"><s>$23.00</s>$19.00</div>
  <div class="btn" style="left:35px;top:350px;width:153px;height:39px">Add To Cart</div>
</div>

<!-- Testimonials -->
<section class="abs" role="img" aria-label="Soft faded photo of a rider with a horse in a stable" style="left:0;top:2498px;width:1200px;height:672px;background:linear-gradient(90deg,#efe4dc 0%,var(--testi-bg) 40%,#e6d6ca 70%,#efe4dc 100%)"></section>
<h2 class="section-title display" style="top:2578px">CLIENT TESTIMONIALS</h2>
<svg class="divider" style="top:2634px" viewBox="0 0 200 8"><path d="M0 4h20M30 4h20M60 4h80M150 4h20M180 4h20" stroke="#c9a67a" stroke-width="3"/></svg>
<div class="abs" style="left:207px;top:2702px;width:790px;height:382px;border:7px solid var(--frame);text-align:center">
  <h3 class="display" style="margin-top:34px;font-size:32px">OLIVER GRANT</h3>
  <p style="font-size:14px;color:var(--muted);margin-top:4px">Lorem Ipsum</p>
  <p style="width:660px;margin:24px auto 0;font-size:15px;line-height:23px">Sed ut perspiciatis unde omnis iste natus error sit voluptatem accusantium doloremque laudantium, totam rem aperiam, eaque ipsa quae ab illo inventore veritatis et quasi architecto beatae vitae dicta sunt explicabo. Nemo enim ipsam voluptatem quia voluptas sit aspernatur aut odit aut fugit, sed quia consequuntur magni dolores eos qui ratione<br>voluptatem sequi nesciunt.</p>
  <svg style="display:block;margin:22px auto 0" width="80" height="66" viewBox="0 0 80 66"><path d="M4 4h30v30c0 16-10 28-26 30l-2-10c9-2 13-8 13-16H4z M44 4h30v30c0 16-10 28-26 30l-2-10c9-2 13-8 13-16H44z" fill="#b89272"/></svg>
</div>
<div class="btn" style="left:79px;top:2867px;width:64px;height:52px"><svg width="14" height="20" viewBox="0 0 14 20"><path d="M11 2L3 10l8 8" fill="none" stroke="#3a2a20" stroke-width="3"/></svg></div>
<div class="btn" style="left:1056px;top:2867px;width:64px;height:52px"><svg width="14" height="20" viewBox="0 0 14 20"><path d="M3 2l8 8-8 8" fill="none" stroke="#3a2a20" stroke-width="3"/></svg></div>

<!-- Blog -->
<h2 class="section-title display" style="top:3253px">LATEST BLOG</h2>
<svg class="divider" style="top:3310px" viewBox="0 0 200 8"><path d="M0 4h20M30 4h20M60 4h80M150 4h20M180 4h20" stroke="#c9a67a" stroke-width="3"/></svg>
<p class="lead" style="top:3348px">Lorem ipsum dolor sit amet, consectetur adipiscing elit, sed do eiusmod<br>ut labore et dolore magna aliqua. Quis ipsum suspendisse ultrices gravida. Risus commodo viverra</p>

<article class="post" style="left:110px">
  <div role="img" aria-label="Hands holding cups of latte art coffee" style="height:190px;background:linear-gradient(135deg,#6b4a35,#c89a72 50%,#5a3e2c)"></div>
  <h5>Lorem ipsum dolor sit ame, consectetur</h5>
  <p>Lorem ipsum dolor sit amet, consectetur adipiscing elit, sed do eiusmod tempor incididunt ut labore et dolore magna aliqua uis ipsum suspendisse ultrices</p>
</article>
<article class="post" style="left:450px">
  <div role="img" aria-label="Roasted coffee beans falling" style="height:190px;background:radial-gradient(ellipse at 50% 45%,#a8663a,#4a2616 60%,#2a140b)"></div>
  <h5>Lorem ipsum dolor sit ame, consectetur</h5>
  <p>Lorem ipsum dolor sit amet, consectetur adipiscing elit, sed do eiusmod tempor incididunt ut labore et dolore magna aliqua uis ipsum suspendisse ultrices</p>
</article>
<article class="post" style="left:789px">
  <div role="img" aria-label="Barista pouring milk into a coffee cup" style="height:190px;background:linear-gradient(135deg,#3a2a22,#8a6a55 55%,#d79a5a)"></div>
  <h5>Lorem ipsum dolor sit ame, consectetur</h5>
  <p>Lorem ipsum dolor sit amet, consectetur adipiscing elit, sed do eiusmod tempor incididunt ut labore et dolore magna aliqua uis ipsum suspendisse ultrices</p>
</article>

<!-- Footer -->
<footer class="abs" style="left:0;top:3893px;width:1200px;height:276px;background:var(--footer-bg)">
  <div class="abs" style="left:0;top:70px;width:1200px;text-align:center;font-size:24px;font-weight:500;color:var(--ink);line-height:32px">Merry Meadow<br>Roasters</div>
  <div class="abs" style="left:0;top:231px;width:1200px;height:1px;background:#d8ccc4"></div>
  <p class="abs" style="left:0;top:245px;width:1200px;text-align:center;font-size:13px">Copyright © 2025 Merry Meadow Roasters. All rights reserved.</p>
</footer>
<div class="foot-links">
  <a style="left:342px">Home</a>
  <a style="left:447px">Shop</a>
  <a style="left:545px">About Us</a>
  <a style="left:672px">Blog</a>
  <a style="left:765px">Contact Us</a>
</div>

</body>
</html>
```